RW Framewell Inc Business cards

We need business cards using our existing logo but slightly modified. Right now the logo says RW Loadbearing Masonry. We want to keep the RW part of the design, but replace the Structural Concrete portion with "FRAMEWELL". Please see the attached file.
Ideally this would be a blank template so we can add Different Names, titles, and phone numbers later.
On the one side we want only the logo and on the other side the detail. I'm attaching an example for you to see.
Please reach out with any other questions. Our address and other details will be given out once we find a design we like.

Target Market(s)

Construction Industry

```html
<!DOCTYPE html>
<html lang="en">
<head>
<meta charset="utf-8">
<title>RW Framewell Inc — Business Cards</title>
<link rel="stylesheet" href="https://fonts.googleapis.com/css2?family=Montserrat:wght@500;600&family=Roboto:wght@400;500;700&display=swap">
<style>
  :root {
    --bg: #d6d6d6;
    --card: #fbfbfb;
    --blue: #2f63ad;
    --grey: #6b6b6b;
    --text-grey: #555555;
    --white: #ffffff;
  }
  * { box-sizing: border-box; margin: 0; padding: 0; }
  html, body {
    width: 1200px; height: 852px; overflow: hidden;
    background: var(--bg);
  }
  .stage {
    position: relative; width: 1200px; height: 852px;
    display: flex; align-items: center; justify-content: center; gap: 60px;
  }
  .card {
    position: relative; width: 510px; height: 296px;
    background: var(--card); border-radius: 22px; overflow: hidden;
    box-shadow: 0 6px 14px rgba(0,0,0,0.18);
  }
  .wordmark {
    display: flex; align-items: center; gap: 12px;
    font-family: "Montserrat", sans-serif; font-weight: 600;
    color: var(--blue); letter-spacing: 0.06em; text-transform: uppercase;
    white-space: nowrap;
  }
  .wordmark-square { width: 18px; height: 18px; background: var(--grey); flex: none; }

  /* Front */
  .card-front .wordmark {
    position: absolute; left: 0; right: 0; top: 118px;
    justify-content: center; font-size: 36px;
  }
  .edge-band {
    position: absolute; left: 0; right: 0; bottom: 0; height: 12px; display: flex;
  }
  .edge-band-grey { flex: 0 0 62%; background: var(--grey); }
  .edge-band-blue { flex: 1; background: var(--blue); }

  /* Back */
  .card-back .wordmark {
    position: absolute; right: 28px; top: 30px; font-size: 24px;
  }
  .waves { position: absolute; inset: 0; }
  .holder {
    position: absolute; left: 30px; top: 112px;
    font-family: "Roboto", sans-serif;
  }
  .holder-name { font-size: 20px; font-weight: 700; color: var(--blue); }
  .holder-title { font-size: 12px; color: var(--text-grey); margin-top: 2px; }
  .address {
    position: absolute; left: 30px; top: 190px;
    font-family: "Roboto", sans-serif; font-size: 13px; line-height: 1.4; color: var(--text-grey);
  }
  .contacts {
    position: absolute; right: 22px; top: 146px; list-style: none;
    font-family: "Roboto", sans-serif; font-size: 13px; color: var(--white);
  }
  .contacts li {
    display: flex; align-items: center; justify-content: flex-end; gap: 7px;
    line-height: 21px; white-space: nowrap;
  }
  .contacts svg { width: 12px; height: 12px; flex: none; fill: none; stroke: var(--white); stroke-width: 1.6; }
</style>
</head>
<body>
<main class="stage">
  <section class="card card-front" aria-label="Card front">
    <div class="wordmark"><span class="wordmark-square"></span>RW Framewell</div>
    <div class="edge-band"><span class="edge-band-grey"></span><span class="edge-band-blue"></span></div>
  </section>

  <section class="card card-back" aria-label="Card back">
    <svg class="waves" viewBox="0 0 510 296" aria-hidden="true">
      <path class="wave-panel" d="M0,296 L0,280 C120,282 200,262 240,200 C270,150 300,112 360,100 C400,92 450,90 510,88 L510,296 Z" fill="var(--blue)"/>
      <path class="wave-stripe" transform="translate(-12,-14)" d="M-20,281 C120,282 200,262 240,200 C270,150 300,112 360,100 C400,92 450,90 540,87" fill="none" stroke="var(--grey)" stroke-width="8"/>
      <path class="wave-line" transform="translate(-4,-6)" d="M90,283 C160,280 210,258 240,200" fill="none" stroke="var(--grey)" stroke-width="2.5" stroke-linecap="round"/>
    </svg>
    <div class="wordmark"><span class="wordmark-square"></span>RW Framewell</div>
    <div class="holder">
      <p class="holder-name">Alex RW Carter</p>
      <p class="holder-title">Managing Director</p>
    </div>
    <p class="address">48 Sample Ave., Any Town,<br>California, US 000000</p>
    <ul class="contacts">
      <li>555-010-2040
        <svg viewBox="0 0 12 12"><path d="M2.5 1.5 L4.5 1.5 L5.3 4 L4 5 C4.6 6.4 5.6 7.4 7 8 L8 6.7 L10.5 7.5 L10.5 9.5 C6 10 2 6 2.5 1.5 Z"/></svg></li>
      <li>framewell-build.com
        <svg viewBox="0 0 12 12"><rect x="1" y="2.5" width="10" height="7"/><path d="M1 2.5 L6 6.5 L11 2.5"/></svg></li>
      <li>alex@framewell-build.com
        <svg viewBox="0 0 12 12"><circle cx="6" cy="6" r="4.8"/><path d="M1.2 6 H10.8 M6 1.2 C3.5 4 3.5 8 6 10.8 M6 1.2 C8.5 4 8.5 8 6 10.8"/></svg></li>
    </ul>
  </section>
</main>
</body>
</html>
```